Custom Cabinet Shop Needs a website design

Hi,
We need a website for a Custom Cabinet Shop and Cabinet parts manufacturing business.
The business has two sides to it. One side provides custom Kitchens, vanities, entertainment units, offices and what not to homeowners and contractors.
The 2nd side of the business provides built to order cabinet boxes and other parts required to put together a project to other cabinet shops, small contractors looking to install there own cabinets.
Website will need a Gallery to display work.
Color scheme to go well with logo.
current website is www.brambleoakcustomcabinets.com
being changed to www.brambleoak.ca
Logo Included in attached files.
Tagline "Joinery with Spirit"
Mission Statement "Our passion is to deliver inspired cabinetry solutions to suit all your needs, supported by our phenomenal star class customer service"
The website should convey quality and professionalism.
Thank you.
Homeowners/ Contractors
Entertainment

```html
<!DOCTYPE html>
<html lang="en">
<head>
<meta charset="utf-8">
<title>Brambleoak Custom Cabinets</title>
<link rel="stylesheet" href="https://fonts.googleapis.com/css2?family=Roboto+Condensed:wght@400;700&family=Open+Sans:wght@300;400;600&family=Lato:ital@1&family=Mako&display=swap">
<style>
  :root {
    --accent: #e84c1e;
    --ink: #1b1b1b;
    --text: #555555;
    --muted: #777777;
    --nav: #0a0a0a;
    --nav-home: #444444;
    --hero-band: #9b9b9b;
    --gallery-band: #f4f4f4;
    --line: #e3e3e3;
    --footer: #141414;
    --white: #ffffff;
  }
  * { margin: 0; padding: 0; box-sizing: border-box; }
  html, body { width: 859px; height: 1200px; overflow: hidden; background: var(--white); }
  body { position: relative; font-family: "Open Sans", sans-serif; color: var(--text); }
  .abs { position: absolute; }

  .top-rule { left: 0; top: 0; width: 859px; height: 4px; background: var(--nav); }

  .brand { left: 42px; top: 30px; display: flex; align-items: center; gap: 8px; }
  .brand-dot { width: 22px; height: 22px; border-radius: 50%; background: var(--accent); }
  .brand-name { font-family: "Roboto Condensed", sans-serif; font-weight: 700; font-size: 24px; color: var(--ink); letter-spacing: 0.5px; }

  .call { left: 683px; top: 29px; }
  .call-label { left: 719px; top: 28px; font-family: "Roboto Condensed", sans-serif; font-size: 10px; color: #333; }
  .call-number { left: 719px; top: 40px; font-family: "Roboto Condensed", sans-serif; font-size: 16px; color: #333; letter-spacing: 0.3px; }

  .nav { left: 0; top: 88px; width: 859px; height: 35px; background: var(--nav); }
  .nav-home { left: 42px; top: 88px; width: 41px; height: 35px; background: var(--nav-home); display: flex; align-items: center; justify-content: center; }
  .nav-item { top: 88px; height: 35px; line-height: 35px; font-size: 9.5px; color: var(--white); transform: translateX(-50%); letter-spacing: 0.2px; }
  .nav-sep { top: 88px; width: 1px; height: 35px; background: #3a3a3a; }

  .hero-band { left: 0; top: 123px; width: 859px; height: 365px; background: var(--hero-band); }
  .hero-frame { left: 42px; top: 146px; width: 774px; height: 306px; background: var(--white); box-shadow: 0 1px 3px rgba(0,0,0,.2); }
  .hero-photo {
    left: 52px; top: 155px; width: 756px; height: 287px;
    background:
      radial-gradient(ellipse 38% 22% at 50% 68%, rgba(150,100,60,.55), rgba(150,100,60,0) 100%),
      radial-gradient(ellipse 30% 45% at 85% 45%, rgba(120,80,55,.45), rgba(120,80,55,0) 100%),
      radial-gradient(ellipse 22% 55% at 14% 55%, rgba(40,55,80,.55), rgba(40,55,80,0) 100%),
      linear-gradient(180deg, #1f2230 0%, #2d2520 45%, #3a2a20 70%, #1a1614 100%);
  }
  .hero-title { left: 52px; top: 250px; width: 756px; text-align: center; font-family: "Mako", sans-serif; font-weight: 400; font-size: 27px; color: var(--white); }
  .hero-text { left: 52px; top: 298px; width: 756px; text-align: center; font-family: "Mako", sans-serif; font-size: 13px; color: var(--white); letter-spacing: 0.5px; word-spacing: 1px; }
  .dot { top: 466px; width: 8px; height: 8px; border-radius: 50%; background: #6f6f6f; }
  .dot.is-active { background: var(--white); }

  .section-title { width: 859px; left: 0; text-align: center; font-family: "Roboto Condensed", sans-serif; font-weight: 400; font-size: 18.5px; color: var(--ink); }
  .section-title em { font-style: normal; color: var(--accent); }
  .welcome-title { top: 513px; }
  .mission { left: 0; top: 548px; width: 859px; text-align: center; font-family: "Lato", sans-serif; font-style: italic; font-size: 11.5px; color: var(--accent); }
  .welcome-text { left: 92px; top: 569px; width: 675px; text-align: center; font-size: 9.6px; line-height: 15.5px; color: var(--text); }

  .gallery-band { left: 0; top: 624px; width: 859px; height: 242px; background: var(--gallery-band); }
  .gallery-box { left: 42px; top: 648px; width: 774px; height: 192px; background: var(--white); border: 1px solid var(--line); }
  .thumb { top: 674px; width: 176px; height: 136px; box-shadow: 0 1px 3px rgba(0,0,0,.25); }
  .thumb-1 {
    left: 67px;
    background:
      radial-gradient(ellipse 30% 40% at 62% 50%, rgba(120,118,105,.6), rgba(120,118,105,0)),
      linear-gradient(90deg, #6a6a60 0%, #5c5b52 30%, #2a2624 55%, #1c1a18 100%);
  }
  .thumb-2 {
    left: 250px;
    background:
      radial-gradient(ellipse 40% 20% at 55% 72%, rgba(200,80,60,.45), rgba(200,80,60,0)),
      linear-gradient(180deg, #e6e8ea 0%, #b8c2c4 28%, #9a8a6a 50%, #6a4a36 75%, #4a3428 100%);
  }
  .thumb-3 {
    left: 434px;
    background:
      radial-gradient(ellipse 35% 25% at 50% 72%, rgba(220,225,230,.6), rgba(220,225,230,0)),
      linear-gradient(90deg, #7a3424 0%, #8c6a52 25%, #c8c2b8 60%, #e0dcd4 100%);
  }
  .thumb-4 {
    left: 618px;
    background:
      radial-gradient(ellipse 40% 25% at 52% 30%, rgba(20,20,25,.95), rgba(20,20,25,0)),
      linear-gradient(180deg, #d6ccc8 0%, #b8aeaa 45%, #7a2a22 62%, #5a1c18 100%);
  }
  .gallery-arrow { top: 727px; }

  .services-title { top: 883px; }
  .service-card { top: 926px; width: 364px; height: 172px; background: var(--white); border: 1px solid #ececec; box-shadow: 0 0 6px rgba(0,0,0,.08); }
  .service-name { top: 950px; font-family: "Roboto Condensed", sans-serif; font-weight: 400; font-size: 16px; color: #444; }
  .service-photo { width: 163px; height: 104px; box-shadow: 0 1px 4px rgba(0,0,0,.3); }
  .photo-home {
    top: 970px;
    background:
      radial-gradient(ellipse 30% 25% at 55% 55%, rgba(230,215,190,.55), rgba(230,215,190,0)),
      linear-gradient(180deg, #3a3838 0%, #4c4642 40%, #5a4236 70%, #9a4a22 100%);
  }
  .photo-business {
    top: 967px;
    background:
      radial-gradient(ellipse 30% 35% at 35% 40%, rgba(70,100,160,.7), rgba(70,100,160,0)),
      radial-gradient(ellipse 30% 35% at 72% 40%, rgba(70,100,160,.6), rgba(70,100,160,0)),
      linear-gradient(180deg, #2a2524 0%, #2e2c34 45%, #6a2a22 75%, #d8d2c0 100%);
  }
  .service-text { top: 970px; width: 155px; font-weight: 400; font-size: 9.1px; line-height: 16.4px; color: var(--muted); }
  .service-text span { display: block; text-align: justify; text-align-last: justify; white-space: nowrap; }
  .service-text span.last { text-align-last: left; }
  .read-more { top: 1063px; font-family: "Lato", sans-serif; font-style: italic; font-size: 9.5px; color: var(--accent); text-decoration: underline; }

  .footer { left: 0; top: 1134px; width: 859px; height: 66px; background: var(--footer); }
  .footer-links { left: 42px; top: 1152px; font-size: 8.5px; color: #e6e6e6; }
  .footer-links span.sep { color: #777; margin: 0 6px; }
  .copyright { left: 42px; top: 1171px; font-size: 8px; color: #e6e6e6; }
  .social {
    top: 1154px; width: 24px; height: 24px; border-radius: 50%;
    background: radial-gradient(circle at 40% 35%, #c4c4c4 0%, #9a9a9a 60%, #7e7e7e 100%);
    box-shadow: inset 0 0 0 2px #bdbdbd, 0 1px 2px rgba(0,0,0,.6);
  }
</style>
</head>
<body>
  <div class="abs top-rule"></div>

  <header>
    <div class="abs brand">
      <span class="brand-dot"></span>
      <span class="brand-name">BRAMBLEOAK</span>
    </div>
    <svg class="abs call" width="32" height="32" viewBox="0 0 32 32" aria-hidden="true">
      <circle cx="16" cy="16" r="14" fill="none" stroke="var(--accent)" stroke-width="2"/>
      <path d="M11.5 9.5c1-.6 1.8-.4 2.3.5l1.1 2.2c.4.8.2 1.5-.5 2l-.8.6c.6 1.7 1.8 3.2 3.5 4.3l.7-.7c.6-.6 1.3-.7 2-.3l2.1 1.2c.9.5 1 1.3.4 2.2l-.8 1.1c-.7.9-1.8 1.2-2.9.8-4.5-1.6-7.8-5.3-8.9-9.9-.3-1.1.1-2.2 1-2.8z" fill="var(--accent)"/>
    </svg>
    <div class="abs call-label">Call Us:</div>
    <div class="abs call-number">012-555-0148</div>
  </header>

  <nav>
    <div class="abs nav"></div>
    <div class="abs nav-home">
      <svg width="16" height="14" viewBox="0 0 16 14" aria-hidden="true">
        <path d="M8 0L0 7h2v7h4.5V9.5h3V14H14V7h2z" fill="#fff"/>
      </svg>
    </div>
    <div class="abs nav-item" style="left:129px">GALLERY</div>
    <div class="abs nav-sep" style="left:170px"></div>
    <div class="abs nav-item" style="left:210px">SERVICES</div>
    <div class="abs nav-sep" style="left:250px"></div>
    <div class="abs nav-item" style="left:297px">WARRANTY</div>
    <div class="abs nav-sep" style="left:343px"></div>
    <div class="abs nav-item" style="left:384px">CONTACT</div>
  </nav>

  <section>
    <div class="abs hero-band"></div>
    <div class="abs hero-frame"></div>
    <div class="abs hero-photo" role="img" aria-label="Dark custom kitchen with a live-edge wooden bar, pendant lights and bar stools"></div>
    <h1 class="abs hero-title">Joinery with Spirit</h1>
    <p class="abs hero-text">vitae dicta sunt explicabo Nemo enim ipsam voluptatem quia&nbsp; sit aspernatur odit aut fugit sed</p>
    <span class="abs dot" style="left:406px"></span>
    <span class="abs dot is-active" style="left:419px"></span>
    <span class="abs dot" style="left:432px"></span>
    <span class="abs dot" style="left:445px"></span>
  </section>

  <section>
    <h2 class="abs section-title welcome-title"><em>WELCOME TO</em> BRAMBLEOAK CUSTOM CABINETS</h2>
    <p class="abs mission">“Our passion is to deliver inspired cabinetry solutions to suit all your needs, supported by our phenomenal star class customer service ”</p>
    <p class="abs welcome-text">Beatae vitae dicta sunt explicabo. Nemo enim ipsam voluptatem quia voluptas sit aspernatur aut odit aut fugit, sed quia consequuntur magni dolores eos qui ratione voluptatem sequi nesciunt. Neque porro quisquam est, qui dolorem ipsum quia dolor sit amet, consectetur,</p>
  </section>

  <section>
    <div class="abs gallery-band"></div>
    <div class="abs gallery-box"></div>
    <div class="abs thumb thumb-1" role="img" aria-label="Dark wet bar with tall cabinets and pendant lights"></div>
    <div class="abs thumb thumb-2" role="img" aria-label="Dining nook with wooden table by bright windows"></div>
    <div class="abs thumb thumb-3" role="img" aria-label="Open kitchen with island and white cabinetry"></div>
    <div class="abs thumb thumb-4" role="img" aria-label="Cherry entertainment unit below a wall-mounted television"></div>
    <svg class="abs gallery-arrow" style="left:42px" width="20" height="34" viewBox="0 0 20 34" aria-hidden="true">
      <path d="M0 0A17 17 0 0 1 17 17 17 17 0 0 1 0 34z" fill="#111"/>
      <path d="M10 13l-5 4 5 4z" fill="#fff"/>
    </svg>
    <svg class="abs gallery-arrow" style="left:797px" width="20" height="34" viewBox="0 0 20 34" aria-hidden="true">
      <path d="M19 0A17 17 0 0 0 2 17 17 17 0 0 0 19 34z" fill="#111"/>
      <path d="M10 13l5 4-5 4z" fill="#fff"/>
    </svg>
  </section>

  <section>
    <h2 class="abs section-title services-title"><em>OUR</em> SERVICES</h2>

    <div class="abs service-card" style="left:42px"></div>
    <h3 class="abs service-name" style="left:54px">Residentials</h3>
    <div class="abs service-photo photo-home" style="left:54px" role="img" aria-label="Residential kitchen with island, pendant lights and hardwood floor"></div>
    <p class="abs service-text" style="left:235px">
      <span>we are proud to be involved in the</span>
      <span>custom cabinet market. By employ-</span>
      <span>ing and partnering up with local</span>
      <span>artisans we are able to deliver a</span>
      <span class="last">product that is second to none.</span>
    </p>
    <a class="abs read-more" style="left:344px">Read More</a>

    <div class="abs service-card" style="left:453px"></div>
    <h3 class="abs service-name" style="left:464px">Business</h3>
    <div class="abs service-photo photo-business" style="left:471px" role="img" aria-label="Built-in display cabinet with glass doors and drawers"></div>
    <p class="abs service-text" style="left:645px">
      <span>we are proud to be involved in the</span>
      <span>custom cabinet market. By employ-</span>
      <span>ing and partnering up with local</span>
      <span>artisans we are able to deliver a</span>
      <span class="last">product that is second to none.</span>
    </p>
    <a class="abs read-more" style="left:754px">Read More</a>
  </section>

  <footer>
    <div class="abs footer"></div>
    <div class="abs footer-links">Home<span class="sep">|</span>Gallery<span class="sep">|</span>Services<span class="sep">|</span>Warranty<span class="sep">|</span>Contact</div>
    <div class="abs copyright">Copyrights © 2015. Harlow Lane Studio Privacy Policy All Rights Reserved.</div>
    <span class="abs social" style="left:702px"></span>
    <span class="abs social" style="left:732px"></span>
    <span class="abs social" style="left:762px"></span>
    <span class="abs social" style="left:793px"></span>
  </footer>
</body>
</html>
```